Maple Roster Business Card for recruitment company

We are looking for a Business Card Design that incorporates our personal details and our busines name and logo. We are a specialized search consultancy that recruit Property and Construction professionals.
We would like a business card that stands out and is appealing to the Construction and Property industry as well.

Target Market(s)

people in the construction and property industry

Contact Information for Business Card

Business Name and logo

Font styles to use
Serif

Colors
0094D4
00A9DD
6FCCEA
C7EBF8
E9F6FB

Requirements
Must have
• Business name and logo as well as contact details
Should not have
• No photos of us please

```html
<!DOCTYPE html>
<html lang="en">
<head>
<meta charset="utf-8">
<title>Maple Roster Business Card</title>
<link rel="stylesheet" href="https://fonts.googleapis.com/css2?family=Josefin+Sans:wght@300;400&family=Lato:wght@400;700&display=swap">
<style>
  :root {
    --canvas: #d9d9d9;
    --navy: #073a52;
    --paper: #ffffff;
    --ink-light: #e8f1f5;
    --rule: #1e4d66;
  }
  * { box-sizing: border-box; margin: 0; padding: 0; }
  html, body { width: 1200px; height: 800px; overflow: hidden; }
  body {
    background: var(--canvas);
    font-family: "Lato", sans-serif;
    position: relative;
  }
  .card {
    position: absolute;
    width: 560px;
    height: 320px;
    border-radius: 22px;
    overflow: hidden;
    box-shadow: 0 6px 18px rgba(0,0,0,0.18);
  }
  .card--front { left: 30px; top: 240px; background: var(--navy); }
  .card--back { left: 610px; top: 240px; background: var(--navy); }

  .front__brand-band {
    position: absolute; left: 0; top: 0; width: 100%; height: 150px;
    background: var(--paper);
    display: flex; align-items: center; justify-content: center;
  }
  .front__stitch {
    position: absolute; left: 0; top: 146px; width: 100%;
    border-top: 2px dashed var(--rule);
  }
  .brand-name {
    font-family: "Josefin Sans", sans-serif;
    font-weight: 300;
    font-size: 46px;
    letter-spacing: 3px;
    color: var(--navy);
    text-transform: uppercase;
  }
  .front__details {
    position: absolute; left: 0; top: 150px; width: 100%; height: 170px;
    display: flex; align-items: center; justify-content: center;
    color: var(--ink-light);
  }
  .person { text-align: right; padding-right: 22px; font-size: 15px; line-height: 1.45; }
  .person__name { font-weight: 700; font-size: 21px; }
  .divider { width: 0; height: 82px; border-left: 1.5px dashed rgba(232,241,245,0.7); }
  .contact { list-style: none; padding-left: 22px; font-size: 15px; line-height: 1.5; }
  .contact li { display: flex; align-items: center; gap: 8px; }
  .contact svg { width: 13px; height: 13px; fill: var(--ink-light); flex: none; }

  .back__mark {
    position: absolute; left: 0; top: 70px; width: 100%;
    display: flex; align-items: center; justify-content: center; gap: 16px;
  }
  .back__dot {
    width: 34px; height: 34px; border-radius: 50%;
    border: 3px solid var(--ink-light);
  }
  .back__mark .brand-name { color: var(--ink-light); font-size: 40px; }
  .back__web {
    position: absolute; left: 0; bottom: 64px; width: 100%;
    text-align: center; color: var(--ink-light);
    font-size: 16px; letter-spacing: 6px; text-transform: uppercase;
  }
</style>
</head>
<body>
  <section class="card card--front">
    <div class="front__brand-band"><span class="brand-name">Maple Roster</span></div>
    <div class="front__stitch"></div>
    <div class="front__details">
      <div class="person">
        <div class="person__name">Daniel Hart</div>
        <div>President</div>
        <div>4120 Cedar Bend Road</div>
        <div>Fairbanks, Alaska 99701</div>
      </div>
      <div class="divider"></div>
      <ul class="contact">
        <li><svg viewBox="0 0 16 16"><path d="M3 1h3l1.5 4-2 1.3a9 9 0 0 0 4.2 4.2L11 8.5l4 1.5v3a2 2 0 0 1-2 2A12 12 0 0 1 1 3a2 2 0 0 1 2-2z"/></svg>555-204-7318</li>
        <li><svg viewBox="0 0 16 16"><path d="M4 1h8a1 1 0 0 1 1 1v12a1 1 0 0 1-1 1H4a1 1 0 0 1-1-1V2a1 1 0 0 1 1-1zm1 2v9h6V3z"/></svg>555-619-2045</li>
        <li><svg viewBox="0 0 16 16"><path d="M2 5h12v9H2zm2-4h8v3H4zm1 7h6v2H5z"/></svg>555-337-8162</li>
        <li><svg viewBox="0 0 16 16"><path d="M1 3h14v10H1zm1.5 1.5L8 9l5.5-4.5z"/></svg>daniel@mapleroster.com</li>
      </ul>
    </div>
  </section>

  <section class="card card--back">
    <div class="back__mark">
      <span class="back__dot"></span>
      <span class="brand-name">Maple Roster</span>
    </div>
    <div class="back__web">www.mapleroster.com</div>
  </section>
</body>
</html>
```